Kestrel Facilities Business Card Design

We would now like to design business cards with the new Kestrel Facilities logo

Target Market(s)

Professional

Industry/Entity Type

Professional services

Contact Information for Business Card

Employee name, title, phone number, email address, corporate office address and logo.

Font styles to use
Sans Serif

Colors
0054AA
0677BA
7BADD7
CADEEF
E8F1F8

Requirements
Must have
• My logo
Should not have
• any other pictures or images besides my logo

```html
<!DOCTYPE html>
<html lang="en">
<head>
<meta charset="utf-8">
<title>Kestrel Facilities – Business Card</title>
<link rel="stylesheet" href="https://fonts.googleapis.com/css2?family=Oswald:wght@500&family=Nunito+Sans:wght@400&display=swap">
<style>
  :root {
    --backdrop: #9a9a9a;
    --card-top: #4a4747;
    --card-bottom: #343131;
    --brand-blue: #0a86e6;
    --text-light: #ffffff;
    --ink-dark: #111111;
  }
  * { box-sizing: border-box; margin: 0; padding: 0; }
  html, body {
    width: 1200px; height: 1200px; overflow: hidden;
    background: var(--backdrop);
  }
  .sheet {
    width: 1200px; height: 1200px;
    display: flex; flex-direction: column; align-items: center; justify-content: center;
    gap: 64px;
  }
  .card {
    position: relative;
    width: 900px; height: 514px;
    background: linear-gradient(180deg, var(--card-top), var(--card-bottom));
    overflow: hidden;
  }
  /* Front */
  .contact {
    position: absolute; left: 62px; top: 104px;
    font-family: "Nunito Sans", sans-serif; color: var(--text-light);
  }
  .contact__name {
    font-family: "Oswald", sans-serif; font-weight: 500;
    font-size: 36px; line-height: 1; color: var(--brand-blue);
    letter-spacing: 0.2px;
  }
  .contact__title { font-size: 20px; margin-top: 4px; }
  .contact__address { font-size: 20px; line-height: 25px; margin-top: 32px; }
  .contact__lines { list-style: none; margin-top: 16px; font-size: 20px; line-height: 26px; }
  .contact__lines li { display: flex; align-items: center; gap: 10px; }
  .contact__lines svg { width: 17px; height: 17px; fill: var(--brand-blue); flex: none; }

  .front-brand {
    position: absolute; left: 420px; top: 0; width: 480px; height: 514px;
    display: flex; flex-direction: column; justify-content: center; align-items: flex-start;
    padding-left: 40px;
    font-family: "Oswald", sans-serif; font-weight: 500;
    color: var(--brand-blue); text-transform: uppercase;
    font-size: 92px; line-height: 1.02;
  }
  /* Back */
  .back-brand {
    position: absolute; inset: 0;
    display: flex; align-items: center; justify-content: center; gap: 22px;
  }
  .back-brand__mark { width: 60px; height: 60px; background: var(--ink-dark); }
  .back-brand__name {
    font-family: "Oswald", sans-serif; font-weight: 500;
    color: var(--ink-dark); text-transform: uppercase;
    font-size: 72px; line-height: 1.05;
  }
</style>
</head>
<body>
<main class="sheet">
  <section class="card card--front">
    <div class="contact">
      <h1 class="contact__name">DANIEL REYES</h1>
      <p class="contact__title">President</p>
      <p class="contact__address">1420 Harbor View Drive<br>Fairbanks<br>Alaska 99701</p>
      <ul class="contact__lines">
        <li><svg viewBox="0 0 24 24" aria-hidden="true"><path d="M6.6 10.8a15.1 15.1 0 0 0 6.6 6.6l2.2-2.2a1 1 0 0 1 1-.25 11.4 11.4 0 0 0 3.6.57 1 1 0 0 1 1 1V20a1 1 0 0 1-1 1A17 17 0 0 1 3 4a1 1 0 0 1 1-1h3.5a1 1 0 0 1 1 1c0 1.25.2 2.45.57 3.57a1 1 0 0 1-.25 1z"/></svg>555-014-2290</li>
        <li><svg viewBox="0 0 24 24" aria-hidden="true"><path d="M7 1h10a2 2 0 0 1 2 2v18a2 2 0 0 1-2 2H7a2 2 0 0 1-2-2V3a2 2 0 0 1 2-2zm0 3v14h10V4zm5 15.5a1 1 0 1 0 0 2 1 1 0 0 0 0-2z"/></svg>555-018-7734</li>
        <li><svg viewBox="0 0 24 24" aria-hidden="true"><path d="M2 6h20v12H2zm2 2v.4l8 5 8-5V8l-8 5z"/></svg>info@kestrelfacilities.com</li>
        <li><svg viewBox="0 0 24 24" aria-hidden="true"><circle cx="12" cy="12" r="10"/></svg>www.kestrelfacilities.com</li>
      </ul>
    </div>
    <div class="front-brand">Kestrel<br>Facilities</div>
  </section>

  <section class="card card--back">
    <div class="back-brand">
      <span class="back-brand__mark"></span>
      <span class="back-brand__name">Kestrel<br>Facilities</span>
    </div>
  </section>
</main>
</body>
</html>
```